Brochure for a civil enineering company in A4 format

I need a brochure design for our company TIRO Engineering S.r.l.. We are an engineering consultant company. Our main clients are from the infrastructure industry (geotechnical and underground sectors mainly).
We are looking for a 2 pages (4 faces) fold out design with a glued pocket where we can put individual data sheets.
I need A4 format pages.

Target Market(s)

We are an engineering consultant company. Our main clients are from the infrastructure industry (geotechnical and underground sectors mainly).

Industry/Entity Type

Civil Engineer

Font styles to use
Sans Serif

Requirements
Must have
• Overall: 2 pages in A4 format
Essential style. Bright and modern appearance.
Glued pocket
Logo integrated in a picture on the pocket where I would like to insert a slogan (… tiro engineering … reliable solutions …)
Attached are selected images which the designer can use and edit at their own discretion.
Some advice in the following (anyway designers are free to provide their solutions):
Outer sheets:
Front page with name, logo. It could be nice to have the “m” of the logo integrated in a pictures, also a modified picture (I mean modify one of the attached pictures) so to create a general image and do not tie the cover to a specific job.
Back page: offices address and contact email address. Nice to have one space for a slogan.
Inner sheet: text that I upload in the file “inside-sheets”, possibly with pictures on each sheet. In the right faces insert the glued pocket. On this pages insert the section OUR EXPERIENCE ….with a space for a picture of our team.
Nice to have
• Clean and essential design.
Pictures choosing from the atteched ones. Pictures could be modified in a very light manner to make them a general idea of the work ( I mean geotechnical world) without to be immediately linked to a specific site.
Should not have
• excessive frills

```html
<!DOCTYPE html>
<html lang="it">
<head>
<meta charset="utf-8">
<title>TIRO Engineering – Brochure</title>
<link rel="stylesheet" href="https://fonts.googleapis.com/css2?family=Source+Sans+3:wght@300;400;600&display=swap">
<style>
  :root{
    --brown:#7b5f2e;
    --cream:#fbf5e4;
    --tan:#c6a96c;
    --ink:#2b2518;
    --rule:#3a3a3a;
    --photo-a:#e9dcbc;
    --photo-b:#8a7350;
  }
  *{margin:0;padding:0;box-sizing:border-box}
  html,body{width:860px;height:1200px;overflow:hidden;background:#fff}
  body{position:relative;font-family:"Source Sans 3",sans-serif;color:var(--ink)}
  .spread{position:absolute;left:40px;width:765px;border:1px solid var(--rule)}
  .spread--outer{top:41px;height:542px}
  .spread--inner{top:602px;height:541px}
  .panel{position:absolute;top:0;height:100%;width:50%;overflow:hidden}
  .panel--left{left:0}
  .panel--right{left:50%;border-left:1px solid var(--rule)}
  .panel--back{background:var(--brown)}
  .panel--front,.panel--company,.panel--expertise{background:var(--cream)}

  .offices{position:absolute;left:179px;top:398px;color:var(--cream);font-size:6px;line-height:7.8px;font-weight:300}
  .offices__title{font-size:6px;letter-spacing:1.4px;text-decoration:underline;margin-bottom:6px;font-weight:400}
  .offices__city{font-weight:600;margin-top:7px}
  .offices__web{margin-top:8px}
  .offices__web b{font-weight:600}

  .cover-photo{position:absolute;inset:0;background:linear-gradient(180deg,#f2e9d1 0%,#eadcb9 40%,#a58c62 70%,#7a6440 100%)}
  .brand{position:absolute;text-align:center}
  .brand__name{font-weight:600;line-height:1;letter-spacing:1px}
  .brand__slogan{font-weight:400;letter-spacing:2.6px;text-transform:uppercase}
  .brand--cover{left:80px;top:55px;width:230px;color:var(--brown)}
  .brand--cover .brand__name{font-size:58px}
  .brand--cover .brand__slogan{font-size:6.4px;margin-top:4px}
  .brand--pocket{left:60px;top:25px;width:250px;color:var(--cream)}
  .brand--pocket .brand__name{font-size:56px}
  .brand--pocket .brand__slogan{font-size:6.4px;margin-top:4px}

  h2{font-weight:300;color:var(--tan);line-height:.95;letter-spacing:.3px}
  .copy{font-size:5.6px;line-height:8.3px}
  .copy p{margin:0}

  .company{position:absolute;left:36px;top:36px;width:162px}
  .company h2{font-size:25px;margin-bottom:3px}
  .photo{position:absolute}
  .photo--tunnel{left:206px;top:0;width:176px;height:217px;background:linear-gradient(160deg,#d9c8a2,#8a7350 55%,#4a3c25)}
  .photo--site{left:36px;top:420px;width:346px;height:121px;background:linear-gradient(180deg,#e6d9b8 0%,#b49d74 50%,#6a5638 100%)}
  .services{position:absolute;left:36px;top:236px;width:340px}
  .services h2{font-size:25px;margin-bottom:3px}
  .services__cols{display:flex;gap:12px}
  .services__intro{width:162px}
  .services__list{width:144px;list-style:none;padding-left:8px}
  .services__list li{position:relative;margin-bottom:4px}
  .services__list li::before{content:"•";position:absolute;left:-7px}

  .expertise{position:absolute;left:44px;top:34px;width:296px}
  .expertise h2{font-size:25px;margin-bottom:9px}
  .expertise .copy{column-count:2;column-gap:15px;height:270px}
  .pocket{position:absolute;left:23px;top:371px;width:360px;height:170px;background:var(--brown);border-top-left-radius:48px;border-top:1px solid var(--rule);border-left:1px solid var(--rule)}
</style>
</head>
<body>

<section class="spread spread--outer">
  <div class="panel panel--left panel--back">
    <address class="offices" style="font-style:normal">
      <div class="offices__title">OUR OFFICES</div>
      <div class="offices__city">Milano</div>
      <div>Via Verdi, 14</div>
      <div>20100 Milano&nbsp; - IT</div>
      <div>T: +39 02 555014477</div>
      <div>E: info@ tiro-eng.example</div>
      <div class="offices__city">Arco TN</div>
      <div>Via S. Marco, 9</div>
      <div>32000 Arco TN - IT</div>
      <div>T: +39 02 555014477</div>
      <div>E: info@ tiro-eng.example</div>
      <div class="offices__web">Web: <b>www.tiro-eng.example</b></div>
    </address>
  </div>
  <div class="panel panel--right panel--front">
    <div class="cover-photo" role="img" aria-label="Sepia construction site with concrete viaduct and scaffolding, faded at the top"></div>
    <div class="brand brand--cover">
      <div class="brand__name">tiro</div>
      <div class="brand__slogan">tiro engineering , reliable solutions</div>
    </div>
  </div>
</section>

<section class="spread spread--inner">
  <div class="panel panel--left panel--company">
    <div class="photo photo--tunnel" role="img" aria-label="Sepia photo of a tunnel boring machine shield lifted by a crane into a shaft"></div>
    <div class="company">
      <h2>OUR COMPANY</h2>
      <div class="copy">
        <p>TIRO Engineering S.r.l. offre servizi di consulenza tecnica, contrattuale e strategica ai principali attori nei settori delle scienze geologiche, dell’ingegneria geotecnica e dell’ingegneria idraulica. Lavoriamo per mitigare il rischio e ridurre l’incertezza, con flessibilità nella ricerca della soluzione ottimale contribuendo ad aumentare la redditività del progetto.</p>
        <p>TIRO Engineering S.r.l. è una società indipendente che nasce nel luglio 2020 dall’associazione di un gruppo di professionisti che hanno messo a fattor comune la reciproca esperienza maturata in oltre trent’anni di attività come progettisti e consulenti nel settore delle grandi opere di ingegneria civile lavorando come Direttori Tecnici di Main Engineering Companies and as Freelancers.</p>
        <p>TIRO Engineering S.r.l. vuole unire l’esperienza dei Fondatori e delle figure chiave con l’entusiasmo di chi intraprende una nuova attività, per dare vita ad una nuova realtà che si pone come obbiettivo principale il design of infrastructures that are safe, sustainable and economic.</p>
        <p>Each of our projects represents a long term commitment, we believe in providing safe, reliable, sustainable end innovative solutions. This is and will be our distinctive characteristic.</p>
      </div>
    </div>
    <div class="services">
      <h2>OUR SERVICES</h2>
      <div class="services__cols copy">
        <div class="services__intro">
          <p>Progettazione e consulenza specialistica nel campo della geologia, dell’ingegneria geotecnica, delle opere sotterranee e dell’ingegneria idraulica.</p>
          <p>Aiutiamo i nostri clienti a risolvere problemi di natura progettuale, contrattuale e costruttiva che possono nascere nell’intera vita del progetto portando la nostra esperienza all’interno delle loro organizzazioni, migliorando la qualità dei loro servizi di ingegneria, ottimizzando i loro progetti, proponendo nuove idee e soluzioni, rafforzando i loro approcci ……</p>
          <p>TIRO Engineering è in grado di fornire la propria assistenza nell’intero iter procedurale, dalla fase di indagine preliminare e di analisi di fattibilità fino alla progettazione costruttiva e all’assistenza tecnica in fase realizzativa.</p>
          <p>La specializzazione e l’esperienza accumulate nelle discipline della geologia, dell’ingegneria geotecnica e del sottosuolo e dell’idraulica ci permette di massimizzare la nostra efficacia quando sia necessario:</p>
        </div>
        <ul class="services__list">
          <li>far fronte a situazioni di emergenza anche su progetti in fase di sviluppo avanzato garantendo l’immediata focalizzazione delle problematiche di progetto e garantendo il risultato finale atteso (in termini di qualità, tempistiche e costi…)</li>
          <li>fornire “second opinion” di elevato valore tecnico ed amministrativo in occasione di problematiche progettuali e costruttive e dispute legali</li>
          <li>analizzare in tempi brevi progetti svolti da terzi individuandone le “criticità”, verificandone la cantierabilità e la validità tecnico economica.</li>
          <li>ottimizzare i progetti redatti da terzi implementandone il contenuto e massimizzando l’efficacia economica degli investimenti.</li>
        </ul>
      </div>
    </div>
    <div class="photo photo--site" role="img" aria-label="Sepia photo of an excavator at an earthworks site with sheet pile wall and trees"></div>
  </div>

  <div class="panel panel--right panel--expertise">
    <div class="expertise">
      <h2>OUR EXPERTISE AND<br>EXPERIENCE</h2>
      <div class="copy">
        <p>La società nasce dall’associazione di un gruppo di professionisti, con indiscusse competenze ed affidabilità, con esperienza maturata in oltre trent’anni di attività come progettisti e consulenti nel settore delle grandi opere di ingegneria civile; geologia, ingegneria geotecnica ed idraulica ed opere sotterranee sono il “core” delle loro competenze ….</p>
        <p>I soci fondatori sono:</p>
        <p>Marco. Già Direttore Tecnico e Socio di NORV Srl, nel periodo di sua permanenza fino al dicembre 2018, ha per essa firmato tutti i progetti nel campo delle opere sotterranee e la maggior parte di quelli di ingegneria geotecnica. Da gennaio 2019 è Direttore Tecnico di TGSA. Può vantare più di 150 gallerie naturali, e numerosi progetti ed assistenze tecniche nel campo delle strutture geotecniche, delle sistemazioni idrogeologiche e dei versanti e delle opere di protezione ambientale. Negli ultimi dieci anni è stato responsabile di attività di assistenza tecnica, per imprese di costruzione, di opere il cui valore supera i 440 Mio EUR e di servizi di progettazione definitiva e/o esecutiva per opere il cui valore supera i 1.400 Mio EUR. Ha svolto attività di verifica e validazione, in Italia ed all’estero, di numerosi progetti il cui valore complessivo supera i 3.400 Mio EUR.</p>
        <p>Piero 30 anni di esperienza professionale. Coinvolto in più di 150 gallerie naturali con lunghezza complessiva superiore a 360 km. Numerosi progetti ed attività di assistenza tecnica nel campo delle strutture, delle sistemazioni idrogeologiche e dei versanti e delle opere di protezione ambientale. Negli ultimi dieci anni responsabile di attività di assistenza tecnica in corso d’opera, per imprese di costruzione, di opere il cui valore supera i 440 Mio EUR e di servizi di progettazione definitiva o esecutiva per opere il cui valore supera i 1.400 Mio EUR. Ha svolto attività di verifica ai fini della validazione, in Italia ed all’estero, di numerosi progetti il cui valore complessivo supera i 3.400 Mio EUR.</p>
        <p>Giulia 30 anni di esperienza professionale. Coinvolta in più di 150 gallerie naturali con lunghezza complessiva superiore a 360 km. Numerosi progetti ed attività di assistenza tecnica nel campo delle strutture, delle sistemazioni idrogeologiche e dei versanti e delle opere di protezione ambientale. Negli ultimi dieci anni responsabile di attività di assistenza tecnica in corso d’opera, per imprese di costruzione, di opere il cui valore supera i 440 Mio EUR e di servizi di progettazione definitiva o esecutiva per opere il cui valore supera i 1.400 Mio EUR. Ha svolto attività di verifica ai fini della validazione, in Italia ed all’estero, di numerosi progetti il cui valore complessivo supera i 3.400 Mio EUR.</p>
        <p>Elena 30 anni di esperienza professionale. Coinvolta in più di 150 gallerie naturali con lunghezza complessiva superiore a 360 km. Numerosi progetti ed attività di assistenza tecnica nel campo delle strutture, delle sistemazioni idrogeologiche e dei versanti e delle opere di protezione ambientale. Negli ultimi dieci anni responsabile di attività di assistenza tecnica in corso d’opera, per imprese di costruzione, di opere il cui valore supera i 440 Mio EUR e di servizi di progettazione definitiva o esecutiva per opere il cui valore supera i 1.400 Mio EUR. Ha svolto attività di verifica ai fini della validazione, in Italia ed all’estero, di numerosi progetti il cui valore complessivo supera i 3.400 Mio EUR.</p>
      </div>
    </div>
    <div class="pocket">
      <div class="brand brand--pocket">
        <div class="brand__name">tiro</div>
        <div class="brand__slogan">tiro engineering , reliable solutions</div>
      </div>
    </div>
  </div>
</section>

</body>
</html>
```